My Business is Car Dealership, we sale cars and trucks, I’m looking for a sign design
I need 2 signage
9ā€ by 7ā€ feet.
the other sign is 3" feet high and the width is 12" feet

For further reference about the company , you can check my website
www.harrowvaleautosale.com

Industry/Entity Type

Business

Requirements
Must have
• picture of 2018 brask T390 or 2018 Dunmoreau Tallwind
Nice to have
• the business name Harrow Vale Auto Sale visible from far distance

```html
<!DOCTYPE html>
<html lang="en">
<head>
<meta charset="utf-8">
<title>Harrow Vale Auto Sale – Roadside Sign 9x7 ft</title>
<link rel="stylesheet" href="https://fonts.googleapis.com/css2?family=Russo+One&family=Cabin:wght@600;700&family=Montserrat:wght@600;700&display=swap">
<style>
  :root {
    --sign-black: #080808;
    --brand-red: #ee1c25;
    --text-white: #ffffff;
    --band-grey: #6a6a6a;
    --page-bg: #ffffff;
    --car-red-light: #f0303a;
    --car-red-dark: #8c0d14;
  }
  * { margin: 0; padding: 0; box-sizing: border-box; }
  html, body {
    width: 1200px; height: 1200px; overflow: hidden;
    background: var(--page-bg);
  }
  .sign {
    position: absolute; left: 100px; top: 211px;
    width: 1000px; height: 778px;
    background: var(--sign-black);
    overflow: hidden;
  }
  .headline {
    position: absolute; left: 0; right: 0; top: 32px;
    text-align: center;
    font-family: "Russo One", sans-serif;
    font-size: 96px; line-height: 1;
    font-style: italic;
    letter-spacing: 8px;
    color: var(--brand-red);
  }
  .subhead-band {
    position: absolute; left: 97px; top: 133px;
    width: 798px; height: 69px;
    clip-path: polygon(8% 0, 100% 0, 92% 100%, 0 100%);
    background: linear-gradient(90deg, rgba(106,106,106,0) 0%, var(--band-grey) 40%, var(--band-grey) 65%, rgba(106,106,106,0) 100%);
  }
  .subhead {
    position: absolute; left: 97px; width: 798px; top: 134px;
    text-align: center;
    font-family: "Cabin", sans-serif; font-weight: 700;
    font-size: 62px; line-height: 1.1;
    color: var(--text-white);
    letter-spacing: -0.5px;
  }
  .vehicle-photo {
    position: absolute; left: 148px; top: 222px;
    width: 673px; height: 300px;
    border-radius: 44% 56% 30% 30% / 55% 45% 40% 40%;
    background: radial-gradient(ellipse at 45% 55%, var(--car-red-light) 0%, #c71820 50%, var(--car-red-dark) 80%, rgba(8,8,8,0) 100%);
  }
  .name-mark {
    position: absolute; left: 214px; top: 550px;
    width: 60px; height: 60px;
    border: 5px solid var(--brand-red);
    border-radius: 50%;
  }
  .dealer-name {
    position: absolute; left: 302px; top: 550px;
    font-family: "Cabin", sans-serif; font-weight: 700;
    font-size: 56px; line-height: 1;
    letter-spacing: 2px;
    color: var(--brand-red);
    white-space: nowrap;
  }
  .phone {
    position: absolute; left: 0; right: 0; top: 612px;
    text-align: center;
    font-family: "Montserrat", sans-serif; font-weight: 700;
    font-size: 92px; line-height: 1;
    letter-spacing: 14px;
    color: var(--text-white);
    padding-left: 14px;
  }
  .website {
    position: absolute; left: 0; right: 0; top: 716px;
    text-align: center;
    font-family: "Montserrat", sans-serif; font-weight: 600;
    font-size: 24px; line-height: 1;
    letter-spacing: 17px;
    color: var(--text-white);
    padding-left: 17px;
  }
  .website .accent { color: var(--brand-red); }
</style>
</head>
<body>
  <main class="sign">
    <h1 class="headline">Quick Cash</h1>
    <div class="subhead-band"></div>
    <p class="subhead">for Your Car or Truck</p>

    <div class="vehicle-photo" role="img" aria-label="Photo of a red sports car with black racing stripes, three-quarter front view"></div>

    <span class="name-mark" aria-hidden="true"></span>
    <p class="dealer-name">Harrow Vale Auto Sale</p>
    <p class="phone">555-014-2700</p>
    <p class="website">www.<span class="accent">harrow</span>vale<span class="accent">auto</span>sale<span class="accent">.com</span></p>
  </main>
</body>
</html>
```